Brindovalle Business cards

Dear team, I need to get the design file to suit it to our team. The focus of the business card is the Automotive Market and the design must be in black colour and the logo must be in glossy black. On the front of the card I need to get the following info:

- Name and Surname
- Title
- eMail
- Phone Number
- Skype account
- domain address

```html
<!DOCTYPE html>
<html lang="en">
<head>
<meta charset="utf-8">
<title>Brindovalle Business Cards</title>
<link href="https://fonts.googleapis.com/css2?family=Rubik:wght@400;500;700&display=swap" rel="stylesheet">
<style>
  :root {
    --backdrop: #d9d9dc;
    --card-black: #121212;
    --pattern-dark: #1c1c1c;
    --pattern-light: #2e2e2e;
    --card-white: #ffffff;
    --brand-red: #e8303a;
    --band-navy: #0d1340;
    --ink: #111111;
    --on-navy: #ffffff;
  }
  * { margin: 0; padding: 0; box-sizing: border-box; }
  html, body { width: 1200px; height: 912px; overflow: hidden; }
  body {
    background: var(--backdrop);
    font-family: "Rubik", sans-serif;
    position: relative;
  }
  .card {
    position: absolute;
    top: 302px;
    width: 540px;
    height: 308px;
    overflow: hidden;
    box-shadow: 0 6px 18px rgba(0,0,0,0.18);
  }
  /* Back side */
  .card--back { left: 40px; background: var(--card-black); }
  .back-pattern {
    position: absolute; inset: 0;
    background: linear-gradient(135deg, var(--pattern-light) 0%, var(--pattern-dark) 55%, var(--card-black) 100%);
  }
  .back-mark {
    position: absolute;
    right: 64px; top: 96px;
    color: var(--brand-red);
    font-weight: 700;
    font-size: 20px;
    letter-spacing: -0.2px;
  }
  /* Front side */
  .card--front { left: 620px; background: var(--card-white); }
  .front-wordmark {
    position: absolute;
    left: 0; right: 0; top: 52px;
    text-align: center;
    color: var(--brand-red);
    font-weight: 700;
    font-size: 44px;
    letter-spacing: -1px;
  }
  .info-band {
    position: absolute;
    left: 0; right: 0; top: 136px;
    height: 76px;
    background: var(--band-navy);
  }
  .person {
    position: absolute;
    left: 8px; top: 14px;
    width: 200px;
    text-align: right;
  }
  .person-name {
    color: var(--brand-red);
    font-weight: 700;
    font-size: 22px;
    letter-spacing: 0.2px;
    line-height: 26px;
    white-space: nowrap;
  }
  .person-title {
    color: var(--on-navy);
    font-size: 13px;
    line-height: 16px;
    margin-top: 2px;
    white-space: nowrap;
  }
  .band-disc {
    position: absolute;
    left: 220px; top: -10px;
    width: 96px; height: 96px;
    border-radius: 50%;
    background: var(--brand-red);
    border: 6px solid var(--card-white);
  }
  .contact-list {
    position: absolute;
    left: 334px; top: 12px;
    list-style: none;
    color: var(--on-navy);
    font-size: 12.5px;
    line-height: 17px;
    white-space: nowrap;
  }
  .contact-list li { display: flex; align-items: center; gap: 6px; }
  .contact-icon { width: 10px; height: 10px; flex: none; }
  .address {
    position: absolute;
    left: 0; right: 0; top: 240px;
    text-align: center;
    color: var(--ink);
    font-size: 14px;
  }
</style>
</head>
<body>
  <section class="card card--back">
    <div class="back-pattern" role="img" aria-label="Repeating glossy black brand-mark pattern"></div>
    <span class="back-mark">Brindovalle</span>
  </section>

  <section class="card card--front">
    <div class="front-wordmark">Brindovalle</div>

    <div class="info-band">
      <div class="person">
        <div class="person-name">MARLON KEATS</div>
        <div class="person-title">Director</div>
      </div>

      <div class="band-disc"></div>

      <ul class="contact-list">
        <li>
          <svg class="contact-icon" viewBox="0 0 10 10"><path d="M2 0.5 L3.6 0.5 L4.2 2.8 L3 3.6 Q4 5.8 6.4 7 L7.2 5.8 L9.5 6.4 L9.5 8 Q9.5 9.5 8 9.5 Q0.5 9 0.5 2 Q0.5 0.5 2 0.5 Z" fill="var(--brand-red)"/></svg>
          555-014-2290
        </li>
        <li>
          <svg class="contact-icon" viewBox="0 0 10 10"><rect x="0.5" y="2" width="9" height="6.5" fill="var(--brand-red)"/><path d="M0.5 2 L5 5.6 L9.5 2" fill="none" stroke="var(--band-navy)" stroke-width="0.9"/></svg>
          info@brindovalle.com
        </li>
        <li>
          <svg class="contact-icon" viewBox="0 0 10 10"><circle cx="5" cy="5" r="4.5" fill="var(--brand-red)"/></svg>
          brindovalle
        </li>
      </ul>
    </div>

    <div class="address">2207 Alder Row, Fenwick, Oregon 97001</div>
  </section>
</body>
</html>
```